Financial Planning business needs a Web Design

Web design needed for financial planning business that encompasses investments, insurance and corporate planning. Would like a sleek, simple design that includes elements of nature/trees and lifestyle based imagery, with an overall feel of trustworthiness, security, growth and freedom. We like the layout of www.quellmarkroanefinancial.example, torvinfinancial.example and plomtavery.example, but with more color and images consistent with the nature/lifestyle theme.

Target Market(s)

New and existing clients

Industry/Entity Type

Financial

Number of Pages Required

5+ page

Requirements
Nice to have
• link to twitter feed
• 'latest features' link to articles
• links to action - buy insurance, get a quote, etc/

```html
<!DOCTYPE html>
<html lang="en">
<head>
<meta charset="utf-8">
<title>Kestrelby Wealth Planning</title>
<link rel="stylesheet" href="https://fonts.googleapis.com/css2?family=Open+Sans:wght@400;600;700&family=Raleway:wght@300;400;500;600&display=swap">
<style>
:root{
  --green:#7cb82f;
  --green-deep:#0d6b3a;
  --green-text:#1f6b3a;
  --dark:#2b2b2b;
  --darker:#222;
  --panel-gray:#dcdcdc;
  --twitter:#1cb3ea;
  --ink:#333;
  --muted:#555;
  --white:#fff;
}
*{margin:0;padding:0;box-sizing:border-box}
html,body{width:898px;height:1200px;overflow:hidden}
body{
  position:relative;
  font-family:"Open Sans",sans-serif;
  color:var(--ink);
  background:radial-gradient(ellipse at 50% 55%,#a8d060 0%,#8cc43c 40%,#6fae28 100%);
}
.abs{position:absolute}
.topbar{top:7px;right:94px;font-size:9px;color:var(--white);display:flex;gap:14px;align-items:center}
.topbar span{display:flex;align-items:center;gap:4px}
.header{left:74px;top:30px;width:750px;height:96px;background:var(--white);box-shadow:0 1px 3px rgba(0,0,0,.15)}
.brand{position:absolute;left:20px;top:10px;display:flex;align-items:center;gap:10px}
.brand-mark{width:46px;height:46px;background:var(--green-deep);border-radius:4px}
.brand-name{font-family:"Raleway",sans-serif;font-weight:500;font-size:24px;color:var(--green-deep);line-height:1}
.brand-sub{font-family:"Raleway",sans-serif;font-weight:500;font-size:10px;letter-spacing:2.2px;color:#666;margin-top:3px}
.nav{position:absolute;top:34px;left:342px;display:flex;font-family:"Open Sans",sans-serif;font-weight:600;font-size:11px;color:var(--green-text)}
.nav a{color:inherit;text-decoration:none;padding:7px 8px 8px;margin-right:7px}
.nav a.active{background:var(--green-deep);color:var(--white);position:relative}
.nav a.active::after{content:"";position:absolute;left:50%;bottom:-5px;margin-left:-5px;border:5px solid transparent;border-bottom:0;border-top-color:var(--green-deep)}
.hero{left:74px;top:134px;width:750px;height:320px;overflow:hidden;
  background:linear-gradient(160deg,#c9ccc0 0%,#e4e5dd 35%,#b9c27a 60%,#6fa12c 80%,#8a7a4a 100%)}
.hero-title{position:absolute;left:70px;top:160px;font-family:"Raleway",sans-serif;font-weight:300;font-size:36px;color:var(--green-text);line-height:1}
.hero-sub{position:absolute;left:70px;top:201px;font-family:"Raleway",sans-serif;font-weight:600;font-size:24px;color:#444;line-height:1}
.dots{position:absolute;left:78px;top:285px;display:flex;gap:5px}
.dots i{width:9px;height:9px;border-radius:50%;background:var(--green-deep)}
.dots i.on{background:#e8601c}
.features{left:74px;top:462px;width:750px;height:263px;background:var(--dark)}
.features h2{font-family:"Raleway",sans-serif;font-weight:400;font-size:16px;color:var(--white);text-align:center;margin-top:10px}
.feature{position:absolute;top:48px;width:238px;text-align:center;color:#ddd}
.feature svg{display:block;margin:0 auto}
.feature h3{font-family:"Open Sans",sans-serif;font-weight:400;font-size:11.5px;letter-spacing:.4px;color:var(--white);margin-top:8px}
.feature p{font-size:9.3px;line-height:19px;margin:9px auto 0;width:180px}
.btn{display:inline-block;border-radius:14px;font-size:8.5px;font-weight:600;color:var(--white);background:#444;height:27px;line-height:27px;width:67px;text-align:center;margin-top:12px}
.btn.green{background:var(--green)}
.divider{position:absolute;top:48px;width:1px;height:196px;background:#3a3a3a}
.welcome{left:74px;top:731px;width:750px;height:248px;background:var(--white)}
.section-title{font-family:"Raleway",sans-serif;font-weight:400;font-size:15px;color:#333}
.portrait{position:absolute;left:6px;top:65px;width:130px;height:183px;background:linear-gradient(180deg,#d9d3cc 0%,#4a4f5a 45%,#1f242c 100%);border-radius:40px 40px 0 0}
.welcome-text{position:absolute;left:144px;top:42px;width:328px;font-size:8.7px;line-height:11.6px;text-align:justify;color:#444}
.welcome-text p+p{margin-top:7px}
.articles{position:absolute;left:502px;top:24px;width:240px}
.article{display:flex;gap:11px;margin-top:0;height:64px}
.date{width:58px;height:56px;background:var(--darker);color:var(--white);text-align:center;flex:none;padding-top:5px;line-height:1}
.date.green{background:var(--green);color:#1c2a10}
.date .y{font-size:7px}
.date .m{font-size:13px;font-weight:700;margin-top:1px}
.date .d{font-size:17px;font-weight:700;margin-top:2px}
.article h4{font-family:"Open Sans",sans-serif;font-weight:400;font-size:11.2px;color:#333;margin-top:4px}
.article p{font-size:8.8px;line-height:11.5px;color:#444;margin-top:3px}
.cta{left:74px;top:990px;width:750px;height:68px;display:flex}
.cta-item{display:flex;align-items:center;padding-left:38px;gap:14px}
.cta-item.buy{width:388px;background:var(--panel-gray);border-left:6px solid var(--darker)}
.cta-item.quote{flex:1;background:var(--white);padding-left:20px}
.cta h5{font-family:"Open Sans",sans-serif;font-weight:700;font-size:15px;color:#222;line-height:1}
.cta p{font-size:8.8px;line-height:11.5px;color:#333;margin-top:4px}
.tweet{left:74px;top:1076px;width:750px;height:41px;background:var(--twitter);color:var(--white);font-size:8.8px;display:flex;align-items:center}
.tweet .badge{width:16px;height:16px;border-radius:50%;background:var(--white);margin:0 14px 0 17px}
.tweet .arrows{position:absolute;right:17px;top:14px;display:flex;gap:2px}
.tweet .arrows i{width:12px;height:13px;background:var(--white);color:#555;font-style:normal;font-size:8px;line-height:13px;text-align:center}
.social{left:700px;top:1134px;display:flex;gap:18px}
.social i{width:14px;height:14px;border-radius:50%;background:var(--white)}
.footer{left:0;top:1165px;width:898px;height:35px;background:var(--darker);color:var(--white);font-size:9px;font-weight:600}
.footer nav{position:absolute;left:76px;top:11px;display:flex;gap:21px}
.footer .copy{position:absolute;right:88px;top:11px;font-weight:400;font-size:8.5px}
</style>
</head>
<body>

<div class="abs topbar">
  <span><svg width="6" height="9" viewBox="0 0 6 9"><rect x=".5" y=".5" width="5" height="8" rx="1" fill="none" stroke="#fff"/></svg>(555) 010 - 2483</span>
  <span><svg width="10" height="8" viewBox="0 0 10 8"><rect x=".5" y=".5" width="9" height="7" fill="none" stroke="#fff"/><path d="M.5 .5 5 4.5 9.5 .5" fill="none" stroke="#fff"/></svg>info@kestrelbywealth.example</span>
</div>

<header class="abs header">
  <div class="brand">
    <div class="brand-mark"></div>
    <div>
      <div class="brand-name">Kestrelby</div>
      <div class="brand-sub">WEALTH PLANNING</div>
    </div>
  </div>
  <nav class="nav">
    <a class="active">Home</a><a>About Us</a><a>What we do</a><a>Articles</a><a>News</a><a>Contact Us</a>
  </nav>
</header>

<section class="abs hero" role="img" aria-label="Close-up photo of a young green seedling growing among coins">
  <div class="hero-title">Kestrelby</div>
  <div class="hero-sub">wealth planning</div>
  <div class="dots"><i></i><i></i><i class="on"></i><i></i><i></i></div>
</section>

<section class="abs features">
  <h2>Latest features</h2>
  <div class="divider" style="left:254px"></div>
  <div class="divider" style="left:496px"></div>
  <div class="feature" style="left:18px">
    <svg width="40" height="38" viewBox="0 0 40 38" fill="#8bc53f">
      <circle cx="20" cy="5" r="4"/><rect x="14" y="10" width="12" height="7" rx="3"/>
      <circle cx="7" cy="20" r="4"/><rect x="1" y="25" width="12" height="9" rx="3"/>
      <circle cx="33" cy="20" r="4"/><rect x="27" y="25" width="12" height="9" rx="3"/>
      <path d="M16 28h8M18 26l-2 2 2 2" stroke="#8bc53f" fill="none" stroke-width="1.5"/>
    </svg>
    <h3>PERSPICIATIS</h3>
    <p>Sed ut peatis unde omnis iste natus error sit votatem accusantium doloremque laudantium.</p>
    <span class="btn green">Read more</span>
  </div>
  <div class="feature" style="left:256px">
    <svg width="34" height="38" viewBox="0 0 34 38" fill="none" stroke="#fff" stroke-width="1.5">
      <rect x="2" y="2" width="30" height="34" rx="2"/>
      <circle cx="11" cy="12" r="3"/><circle cx="23" cy="12" r="3"/><ellipse cx="17" cy="21" rx="7" ry="3"/>
      <circle cx="11" cy="29" r="3"/><circle cx="23" cy="29" r="3"/>
    </svg>
    <h3>VOLUPTATEM</h3>
    <p>Vestibulum libero nisl, porta vel, sceler­isque eget, malesuada at, neque. Vivamus eget nibh.</p>
    <span class="btn">Read more</span>
  </div>
  <div class="feature" style="left:494px">
    <svg width="40" height="38" viewBox="0 0 40 38" fill="#fff">
      <circle cx="6" cy="6" r="3.5"/><rect x="2" y="10" width="8" height="9" rx="2"/>
      <rect x="14" y="2" width="24" height="15" fill="none" stroke="#fff" stroke-width="1.5"/>
      <path d="M17 13l5-4 4 3 8-7" stroke="#fff" fill="none" stroke-width="1.5"/>
      <circle cx="8" cy="24" r="3"/><circle cx="17" cy="24" r="3"/><circle cx="26" cy="24" r="3"/><circle cx="35" cy="24" r="3"/>
      <rect x="4" y="28" width="8" height="7" rx="2"/><rect x="13" y="28" width="8" height="7" rx="2"/><rect x="22" y="28" width="8" height="7" rx="2"/><rect x="31" y="28" width="8" height="7" rx="2"/>
    </svg>
    <h3>ACCUSANTIUM</h3>
    <p>Totam rem aperiam, eaque illo inventore veritatis et quasi architecto beatae vitae dicta.</p>
    <span class="btn">Read more</span>
  </div>
</section>

<section class="abs welcome">
  <h2 class="section-title abs" style="left:20px;top:16px">Welcome To Our Website</h2>
  <div class="portrait" role="img" aria-label="Portrait photo of a smiling advisor in a dark suit"></div>
  <div class="welcome-text">
    <p>Sed ut perspiciatis unde omnis iste natus error sit voluptatem accusantium doloremque laudantium, totam rem aperiam, eaque ipsa quae ab illo inventore veritatis et quasi architecto beatae vitae dicta sunt explicabo. Nemo enim ipsam voluptatem quia voluptas sit aspernatur aut odit aut fugit, sed quia consequuntur magni dolores eos qui ratione voluptatem sequi nesciunt. Neque porro quisquam est, qui dolorem ipsum quia dolor sit amet, consectetur, adipisci velit, Sed ut perspiciatis unde omnis iste natus error sit voluptatem accusantium doloremque laudantium, totam rem aperiam, eaque ipsa quae ab illo inventore veritatis et quasi architecto beatae vitae dicta sunt explicabo. Nemo enim ipsam voluptatem quia voluptas sit aspernatur aut odit aut fugit,</p>
    <p>sed quia non numquam eius modi tempora incidunt ut labore et dolore magnam aliquam quaerat voluptatem. Ut enim ad minima veniam,</p>
  </div>
  <span class="btn green abs" style="left:404px;top:195px;margin:0">Read more</span>

  <div class="articles">
    <h2 class="section-title" style="margin-top:-8px;margin-bottom:13px">Articles</h2>
    <div class="article">
      <div class="date green"><div class="y">2015</div><div class="m">FEB</div><div class="d">20</div></div>
      <div><h4>SED UT PERSPICIATIS UNDE</h4><p>Dolorelaudantium, totam rem aperiam, eaque ipsa quae ab illo.</p></div>
    </div>
    <div class="article">
      <div class="date"><div class="y">2015</div><div class="m">FEB</div><div class="d">20</div></div>
      <div><h4>SED UT PERSPICIATIS UNDE</h4><p>Dolorelaudantium, totam rem aperiam, eaque ipsa quae ab illo.</p></div>
    </div>
    <div class="article">
      <div class="date"><div class="y">2015</div><div class="m">FEB</div><div class="d">20</div></div>
      <div><h4>SED UT PERSPICIATIS UNDE</h4><p>Dolorelaudantium, totam rem aperiam, eaque ipsa quae ab illo.</p></div>
    </div>
  </div>
</section>

<section class="abs cta">
  <div class="cta-item buy">
    <svg width="44" height="38" viewBox="0 0 44 38" fill="none" stroke="#6aaa2a" stroke-width="2">
      <circle cx="22" cy="11" r="9"/><path d="M22 5v12M25 8h-4a2 2 0 0 0 0 4h2a2 2 0 0 1 0 4h-4"/>
      <path d="M4 18c0 8 6 16 14 17l2-6M40 18c0 8-6 16-14 17l-2-6"/>
    </svg>
    <div><h5>BUY INSURANCE</h5><p>Dolorelaudantium, totam rem aperiam,<br>eaque ipsa quae ab illo.</p></div>
  </div>
  <div class="cta-item quote">
    <svg width="42" height="40" viewBox="0 0 42 40" fill="none" stroke="#6aaa2a" stroke-width="2">
      <rect x="2" y="4" width="26" height="32" rx="2"/><path d="M7 12h4M14 12h9M7 19h4M14 19h9M7 26h4"/>
      <path d="M26 18l10 3v7c0 5-5 9-10 10-5-1-10-5-10-10v-7z" fill="#fff"/><path d="M21 27l4 4 7-8"/>
    </svg>
    <div><h5>GET A QUOTE</h5><p>Dolorelaudantium, totam rem aperiam,<br>eaque ipsa quae ab illo.</p></div>
  </div>
</section>

<section class="abs tweet">
  <span class="badge"></span>
  <span>Check out 'Harbor - Civic Campaign Starter Theme' on #MarlowMarket by @quintbuild #themegrove http://lnk.example/r4Tq9</span>
  <div class="arrows"><i>‹</i><i>›</i></div>
</section>

<div class="abs social"><i></i><i></i><i></i><i></i></div>

<footer class="abs footer">
  <nav><span>Home</span><span>About Us</span><span>What we do</span><span>Articles</span><span>News</span><span>Contact Us</span></nav>
  <div class="copy">© 2015 www.kestrelbywealth.example</div>
</footer>

</body>
</html>
```